New corporate stationery design for UK train leasing company

In advance of an office move later this year we are looking to redesign all our corporate stationery (business cards, letterhead, compliment slips, envelopes etc) as well as small branded items (such as mouse mats, drink mats, etc).

We wish to keep the same logo and corporate colours but are looking for a modern, fresh look that will tie in our stationery more with the look of our website and our PowerPoint template. We have a strapline, "Fleet People, Track Knowledge" that we would like to incorporate into the stationery design and also need to include a "TOVEC" logo on the bottom of the letterhead/compliment slips. We have two offices so will need letterhead and compliment slips with both addresses.

The files attached include different versions of our logo (the main one is the black with green halo, file 1 or 3), our brand guidelines summary (including Pantone colours), the TOVEC logo and PowerPoint template.

More information about the business can be found at www.copperlinefleet.co.uk.

If you have any questions please let me know.

I look forward to seeing the designs!
Regards
Harriet

Main audience are train operators, rail industry suppliers, passenger transport groups, government and other political organisations, financiers/lenders.

Business

```html
<!DOCTYPE html>
<html lang="en">
<head>
<meta charset="utf-8">
<title>Copperline Fleet — DL Envelope Stationery</title>
<link href="https://fonts.googleapis.com/css2?family=Arimo:wght@400&display=swap" rel="stylesheet">
<style>
  :root {
    --backdrop: #efefef;
    --paper: #f4f4f4;
    --paper-shade: #e9e9e9;
    --flap-edge: #dcdcdc;
    --ink: #1e1e1e;
    --brand-green: #008b6d;
  }
  * { box-sizing: border-box; margin: 0; padding: 0; }
  html, body {
    width: 1200px;
    height: 795px;
    overflow: hidden;
    background: var(--backdrop);
  }
  .stationery {
    position: relative;
    width: 1200px;
    height: 795px;
    display: flex;
    align-items: center;
    justify-content: center;
    gap: 40px;
  }
  .envelope {
    position: relative;
    width: 540px;
    height: 270px;
    background: var(--paper);
    box-shadow: 0 1px 2px rgba(0,0,0,0.10), 0 6px 18px rgba(0,0,0,0.06);
    overflow: hidden;
  }
  .envelope__band {
    position: absolute;
    left: 0;
    right: 0;
    bottom: 0;
    height: 7px;
    background: var(--brand-green);
  }
  .envelope__flap {
    position: absolute;
    inset: 0;
    width: 100%;
    height: 100%;
  }
  .brand {
    position: absolute;
    left: 34px;
    top: 40px;
    font-family: "Arimo", Arial, sans-serif;
    color: var(--ink);
  }
  .brand__name {
    font-weight: 400;
    font-size: 30px;
    letter-spacing: 0.5px;
    line-height: 1;
  }
  .brand__strapline {
    margin-top: 8px;
    font-size: 8.5px;
    line-height: 1.25;
    letter-spacing: 0.2px;
  }
</style>
</head>
<body>
  <main class="stationery">
    <section class="envelope envelope--back" aria-label="Envelope reverse">
      <svg class="envelope__flap" viewBox="0 0 540 270" aria-hidden="true">
        <path d="M0 0 H540 V0 L540 104 Q540 112 532 112 H14 Q6 112 4 104 L0 92 Z"
              fill="var(--paper-shade)" stroke="var(--flap-edge)" stroke-width="1"/>
      </svg>
      <div class="envelope__band"></div>
    </section>

    <section class="envelope envelope--front" aria-label="Envelope front">
      <div class="brand">
        <p class="brand__name">copperline fleet</p>
        <p class="brand__strapline">Fleet People<br>Track Knowledge</p>
      </div>
      <div class="envelope__band"></div>
    </section>
  </main>
</body>
</html>
```